Lumen Fitness Personal Training Business

I need a business card design with a logo for my personal training company. I'd like the colors to be a vibrant green and black. I'd like the logo to incorporate an anvil (or something similar). I train hardcore competitive athletes as well as soccer moms trying to get and/or stay in shape. I need a logo that will not pigeon hole me in one category or the other, but at the same time not be too intimidating to soccer moms, but will not be off putting to the more hardcore trainees. The design should be attention grabbing and aesthetic.
Target Market(s)
Hardcore athletes as well as average people just trying to get/stay in shape.
Industry/Entity Type
Training

```html
<!DOCTYPE html>
<html lang="en">
<head>
<meta charset="utf-8">
<title>Lumen Fitness – Business Card</title>
<link href="https://fonts.googleapis.com/css2?family=Open+Sans:wght@400;600&display=swap" rel="stylesheet">
<style>
  :root {
    --backdrop: #3a332f;
    --card: #161616;
    --green: #27b34a;
    --green-soft: #3cc85c;
    --silver: #c9c9c9;
    --divider: #2e2e2e;
  }
  * { margin: 0; padding: 0; box-sizing: border-box; }
  html, body { width: 1200px; height: 844px; overflow: hidden; }
  body {
    background: var(--backdrop);
    font-family: "Open Sans", sans-serif;
    position: relative;
  }
  .card {
    position: absolute;
    top: 272px;
    width: 520px;
    height: 300px;
    background: var(--card);
    border-radius: 4px;
  }
  .card-front { left: 60px; }
  .card-back { left: 620px; }

  /* front */
  .brand {
    position: absolute;
    top: 48px;
    left: 50px;
    display: flex;
    align-items: center;
    gap: 16px;
  }
  .brand-mark {
    width: 44px; height: 44px;
    background: var(--green);
    border-radius: 6px;
  }
  .brand-name {
    color: var(--green);
    font-weight: 600;
    font-size: 38px;
    letter-spacing: 1px;
    line-height: 1;
  }
  .identity {
    position: absolute;
    top: 160px;
    left: 50px;
    width: 200px;
    text-align: right;
    color: var(--green);
  }
  .person-name { font-weight: 600; font-size: 19px; line-height: 1.2; }
  .person-role { font-size: 13px; margin-bottom: 18px; }
  .address { font-size: 14px; line-height: 1.3; }
  .divider {
    position: absolute;
    top: 150px;
    left: 268px;
    width: 1px;
    height: 110px;
    background: var(--divider);
  }
  .contacts {
    position: absolute;
    top: 150px;
    left: 288px;
    list-style: none;
  }
  .contact {
    display: flex;
    align-items: center;
    gap: 10px;
    color: var(--green);
    font-size: 14px;
    height: 26px;
  }
  .contact-icon {
    width: 16px; height: 16px;
    background: var(--green);
    border-radius: 3px;
    display: flex;
    align-items: center;
    justify-content: center;
  }
  .contact-icon svg { width: 11px; height: 11px; }

  /* back */
  .back-brand {
    position: absolute;
    inset: 0;
    display: flex;
    align-items: center;
    justify-content: center;
    gap: 18px;
  }
  .back-brand .brand-mark {
    width: 56px; height: 56px;
    background: var(--silver);
  }
  .back-brand .brand-name {
    color: var(--silver);
    font-size: 44px;
  }
</style>
</head>
<body>

<section class="card card-front" aria-label="Business card front">
  <div class="brand">
    <span class="brand-mark" aria-hidden="true"></span>
    <span class="brand-name">Lumen Fitness</span>
  </div>

  <div class="identity">
    <p class="person-name">Daniel Reyes</p>
    <p class="person-role">Managing Director</p>
    <p class="address">12345, Address Goes Here<br>Country Name, 123456</p>
  </div>

  <span class="divider" aria-hidden="true"></span>

  <ul class="contacts">
    <li class="contact">
      <span class="contact-icon" aria-hidden="true">
        <svg viewBox="0 0 12 12"><path d="M2 1h2.5l1 2.5-1.5 1a6 6 0 0 0 3.5 3.5l1-1.5L11 7.5V10a1 1 0 0 1-1 1A9 9 0 0 1 1 2a1 1 0 0 1 1-1z" fill="#161616"/></svg>
      </span>
      (044)-555-0182
    </li>
    <li class="contact">
      <span class="contact-icon" aria-hidden="true">
        <svg viewBox="0 0 12 12"><rect x="3" y="1" width="6" height="10" rx="1" fill="#161616"/><rect x="4" y="2.5" width="4" height="6" fill="#27b34a"/></svg>
      </span>
      123-555-0147
    </li>
    <li class="contact">
      <span class="contact-icon" aria-hidden="true">
        <svg viewBox="0 0 12 12"><rect x="1" y="2.5" width="10" height="7" fill="#161616"/><path d="M1 2.5l5 4 5-4" stroke="#27b34a" fill="none"/></svg>
      </span>
      info@lumenmail.com
    </li>
    <li class="contact">
      <span class="contact-icon" aria-hidden="true">
        <svg viewBox="0 0 12 12"><path d="M5 7l2-2M4.5 5.5l-1.5 1.5a1.8 1.8 0 0 0 2.5 2.5L7 8M7.5 6.5l1.5-1.5a1.8 1.8 0 0 0-2.5-2.5L5 4" stroke="#161616" stroke-width="1.3" fill="none" stroke-linecap="round"/></svg>
      </span>
      www.lumenfit.com
    </li>
  </ul>
</section>

<section class="card card-back" aria-label="Business card back">
  <div class="back-brand">
    <span class="brand-mark" aria-hidden="true"></span>
    <span class="brand-name">Lumen Fitness</span>
  </div>
</section>

</body>
</html>
```